Flyer für Verkauf von Radondetektoren
Zielgruppe
Ich verkaufe Radondetektoren zur Messung von Radon in Innenräumen. Zielgruppe sind Privatpersonen, Firmen, Genossenschaften und andere Hauseigentümer.
Aufgabenstellung
Ich brauche das Design für meine Messanleitung.
Kreativ - modern - weniger kann mehr sein
Struktur ist wichtigt, es soll also einfach sein zu lesen und zu verstehen, was gemacht werden soll. Können Bulletpoints, Icons mit eingebracht werden.
Wichtig ist auch, dass die beiden Logos 'Luftprüfer.de' und TESTOVAL' auf der Messanleitung vorhanden sind. Wobei 'Luftprüfer.de' das Hauptlogo ist.
DIN format dachte ich A4 beidseitig (Text müsste also auf diese Grösse angepasst werden).
Kann natürlich auch Flyer-Format sein oder andere Vorschläge!
Bildmaterial gibt es auf unsere Homepage https://luftprüfer.de und https://luftkontroll.se . Diese haben wir bereits gekauft und können verwendet werden. Ich lade sie den bei Bedarf hoch. Es können natürlich auch andere Vorschläge kommen.

```html
<!DOCTYPE html>
<html lang="de">
<head>
<meta charset="utf-8">
<title>Messanleitung – Luftprüfer.de</title>
<link href="https://fonts.googleapis.com/css2?family=Open+Sans:ital,wght@0,400;0,600;0,700;1,400&family=Raleway:wght@600;700;800&display=swap" rel="stylesheet">
<style>
:root{
  --red:#d0232a;
  --ink:#2b2b2b;
  --text:#4a4a4a;
  --paper:#f7f7f7;
  --header-grey:#e9e9ea;
  --stage:#e8e8e8;
  --partner-blue:#23408f;
}
*{box-sizing:border-box;margin:0;padding:0}
html,body{width:1200px;height:800px;overflow:hidden;background:var(--stage)}
body{font-family:"Open Sans",Arial,sans-serif;color:var(--text);position:relative}
.sheet{position:absolute;top:20px;width:537px;height:760px;background:var(--paper);box-shadow:0 6px 18px rgba(0,0,0,.12);overflow:hidden}
.sheet--front{left:43px}
.sheet--back{left:620px}

p,li{font-size:6.9px;line-height:13.3px}
.red{color:var(--red)}
.strong-red{color:var(--red);font-weight:700}
ul.dots{list-style:none}
ul.dots li{position:relative;padding-left:14px;margin-bottom:5px}
ul.dots li::before{content:"";position:absolute;left:1px;top:4px;width:6px;height:6px;border-radius:50%;background:var(--red)}
.step{display:flex;align-items:center;gap:9px;margin-bottom:8px}
.step-badge{width:24px;height:24px;border-radius:50%;background:var(--red);color:#fff;font-family:"Raleway",sans-serif;font-weight:800;font-size:12px;display:flex;align-items:center;justify-content:center;flex:none}
.step-title{font-family:"Raleway",sans-serif;font-weight:700;font-size:10.5px;color:var(--red);line-height:12px}
.step-sub{font-family:"Raleway",sans-serif;font-weight:800;font-size:7.4px;color:var(--ink);letter-spacing:.2px}
.section-head{border-left:2.5px solid var(--red);padding-left:6px;font-family:"Raleway",sans-serif;font-weight:700;font-size:12.5px;color:var(--ink);line-height:15px;margin:14px 0 12px}
.group-head{display:flex;justify-content:space-between;align-items:center;font-weight:700;font-size:8px;line-height:12px;color:var(--red);margin:10px 0 8px}
.group-head svg{flex:none}

.front-header{height:123px;background:var(--header-grey);position:relative;padding:30px 0 0 25px}
.doc-title{font-family:"Raleway",sans-serif;font-weight:800;font-size:22px;color:var(--red);letter-spacing:.3px;line-height:24px}
.doc-subtitle{font-family:"Raleway",sans-serif;font-weight:600;font-size:12.5px;color:var(--ink);line-height:21px;margin-top:4px}
.header-scene{position:absolute;right:0;bottom:0;width:175px;height:110px;background:linear-gradient(160deg,#dfe5ee 0%,#b7b3d6 40%,#7e74b8 60%,#72a64b 85%,#4d8b34 100%);border-top-left-radius:60px 40px}
.front-body{display:flex;padding:16px 18px 0 25px;height:620px}
.col{flex:1}
.col--left{padding-right:12px}
.col--right{border-left:1.5px solid var(--red);padding-left:16px;height:604px}
.note{font-style:italic;font-size:6.6px;margin-top:6px;margin-bottom:18px}
.front-footer{position:absolute;left:0;right:0;bottom:0;height:9px;background:var(--red)}

.hero{height:184px;position:relative;background:linear-gradient(115deg,#f3ebe3 0%,#e7c7a4 30%,#caa073 55%,#f0d8a8 80%,#f7e7c6 100%)}
.brand{position:absolute;top:26px;right:30px;display:flex;align-items:center;gap:9px}
.brand-dot{width:20px;height:20px;border-radius:50%;background:var(--red);flex:none}
.brand-name{font-family:"Open Sans",sans-serif;font-weight:600;font-size:22px;color:var(--ink);line-height:24px}
.back-body{padding:16px 25px 0 25px}
.step-row{display:flex;justify-content:space-between;align-items:center}
.partner{font-family:"Open Sans",sans-serif;font-weight:600;font-size:17px;color:var(--partner-blue);margin-right:20px;letter-spacing:.5px}
.duration{display:flex;margin-top:10px}
.duration .col--left{padding-right:14px;border-right:1.5px solid var(--red)}
.duration .col--right{border-left:none;height:auto;padding-left:16px}
.duration h3{font-size:8.5px;color:var(--red);font-weight:700;margin-bottom:8px}
.address{display:flex;align-items:center;gap:12px;margin:8px 0 10px}
.address p{font-weight:700;color:var(--red);line-height:13px}
.hints{margin:20px -5px 0;background:var(--red);padding:5px}
.hints-inner{border:1.2px solid #fff;padding:10px 14px 8px}
.hints h4{font-family:"Open Sans",sans-serif;font-weight:700;font-size:9px;color:#fff;margin-bottom:6px}
.hints-cols{display:flex;gap:18px}
.hints ul li{color:#fff;font-size:6.5px;line-height:12.4px}
.hints ul li::before{background:#fff}
.back-footer{position:absolute;left:0;right:0;bottom:0;height:52px;background:var(--red);display:flex;align-items:center;justify-content:center;padding-top:10px}
.back-footer p{color:#fff;font-weight:700;font-size:7px}
</style>
</head>
<body>

<section class="sheet sheet--front">
  <header class="front-header">
    <h1 class="doc-title">MESSANLEITUNG</h1>
    <p class="doc-subtitle">FÜR RADONMESSUNGEN VON INNENRAUMLUFT<br>MIT PASSIVEN RADON DETEKTOREN</p>
    <div class="header-scene" role="img" aria-label="Illustration einer Stadtlandschaft mit Hochhäusern, Wohnhäusern und Bäumen"></div>
  </header>

  <div class="front-body">
    <div class="col col--left">
      <div class="step">
        <span class="step-badge">1</span>
        <div><div class="step-title">SCHRITT 1:</div><div class="step-sub">REGISTRIERUNG UND ANMELDUNG</div></div>
      </div>
      <p>Wenn Sie Neukunde sind, legen Sie bitte zunächst ein neues Benutzerkonto auf unserem Online-Portal <span class="strong-red">https://kundenportal.testoval.se/de an</span>. Anschließend können Sie die Radondetektoren registrieren. Vermerken Sie den Start der Messung (Datum und Uhrzeit), die Messorte (Raum und Etage) sowie die 9-stellige Seriennummer der Detektoren, die Sie auf der Verpackung oder auf der Unterseite der jeweiligen Detektoren finden.</p>
      <p class="note">Firmenkunden haben die Möglichkeit eine Excel-Datei als Hilfsmittel herunterzuladen, die Sie ausfüllen und dann wieder hochladen.</p>

      <div class="step">
        <span class="step-badge">2</span>
        <div><div class="step-title">SCHRITT 2:</div><div class="step-sub">PLATZIERUNG DER DETEKTOREN</div></div>
      </div>
      <p>Bevor Sie die Detektoren der Verpackung entnehmen, überlegen Sie wo genau Sie die Radondetektoren platzieren wollen. Die Radonmessung beginnt, sobald Sie die radondichten Verpackungen öffnen. Beachten Sie bei der Platzierung zunächst die <span class="strong-red">Auswahl der Räume</span> und <span class="strong-red">die Positionierung der Radondetektoren im Raum</span>. Für eine zuverlässige Radonmessung empfehlen wir wie folgt vorzugehen:</p>

      <h2 class="section-head">Die Auswahl der Räume:</h2>

      <div class="group-head">Radonmessungen für Einfamilienhäuser:
        <svg width="28" height="26" viewBox="0 0 28 26" fill="none" stroke="#d0232a" stroke-width="1.3"><path d="M3 12 L14 3 L25 12"/><path d="M6 10 V24 H22 V10"/><rect x="11.5" y="16" width="5" height="8"/><rect x="8" y="13" width="3" height="3"/><rect x="17" y="13" width="3" height="3"/></svg>
      </div>
      <ul class="dots">
        <li>Es sollten mindestens zwei Wohnräume und pro bewohnte Etage mindestens ein Wohnraum gemessen werden. Wählen Sie Räume aus, in denen Sie sich oft aufhalten (z.B. das Wohn- und Schlafzimmer). Vermeiden Sie aber Räume, in denen das Fenster mehrere Stunden am Tag oder in der Nacht geöffnet ist.</li>
        <li>Insofern Sie einen Keller haben, empfehlen wir alle Kellerräume zu messen, da hier meist das größte Risiko einer erhöhten Radonkonzentration erwartet wird.</li>
      </ul>

      <div class="group-head">Radonmessungen für Mehrfamilienhäuser,<br>Wohnungen und Wohnkomplexen:
        <svg width="28" height="30" viewBox="0 0 28 30" fill="none" stroke="#d0232a" stroke-width="1.3"><rect x="5" y="3" width="18" height="25"/><path d="M9 8h3M16 8h3M9 13h3M16 13h3M9 18h3M16 18h3"/><rect x="12" y="22" width="4" height="6"/></svg>
      </div>
      <ul class="dots">
        <li>Alle Wohnungen mit direktem Bodenkontakt sowie mindestens eine Wohnung pro Etage sollten gemessen werden. Wählen Sie dabei Wohnungen, die an Aufzügen oder Luftschächten liegen.</li>
      </ul>
    </div>

    <div class="col col--right">
      <ul class="dots">
        <li>In größeren Wohnkomplexen sollten insgesamt mindestens 20% aller Wohnungen in einem Gebäude gemessen werden.</li>
        <li>Es sollten mindestens zwei Wohnräume pro ausgewählte Wohnung gemessen werden. Wählen Sie Räume aus, in denen Sie sich oft aufhalten (z.B. das Wohn- und Schlafzimmer). Vermeiden Sie aber Räume, in denen das Fenster mehrere Stunden am Tag oder in der Nacht geöffnet ist.</li>
        <li>Selbst bei einer Einzimmerwohnung sollten Sie zwei Detektoren aufstellen.</li>
      </ul>

      <div class="group-head">Radonmessungen für Arbeitsplätze und<br>öffentliche Gebäude:
        <svg width="30" height="28" viewBox="0 0 30 28" fill="none" stroke="#d0232a" stroke-width="1.3"><path d="M3 9 L15 3 L27 9 Z"/><path d="M3 26 H27"/><path d="M7 11v13M12 11v13M18 11v13M23 11v13"/><path d="M5 24h20"/></svg>
      </div>
      <ul class="dots">
        <li>Wählen Sie Räume, die regelmäßig mehr als vier Stunden pro Tag genutzt werden.</li>
        <li>Messen Sie alle unterirdischen Räumlichkeiten, da hier meist das größte Risiko einer erhöhten Radonkonzentration erwartet wird.</li>
        <li>Messen Sie alle Räume im Erdgeschoß. Für größere Räumlichkeiten empfehlen wir einen Detektor pro 200 m².</li>
        <li>In den oberen Etagen sollten Sie mit mindestens zwei Detektoren, sowie mindestens einem Detektor pro 200 m² messen.</li>
      </ul>

      <h2 class="section-head">Platzierung der Detektoren<br>im Raum:</h2>
      <ul class="dots">
        <li>Platzieren Sie die Detektoren in einem Mindestabstand von 20 cm zu Wänden, 50 cm zu Abluftventilen, sowie 1,50 m zu Fenstern, Außentüren, Zuluftventilen und Heizkörpern.</li>
        <li>Stellen Sie die Detektoren nicht auf dem Boden, an starken Wärmequellen oder Luftströmen auf. Vermeiden Sie auch Räume mit hoher Luftfeuchtigkeit, wie zum Beispiel das Badezimmer.</li>
        <li>Die Detektoren können entweder stehend (auf einem Tisch, im Regal oder einer Schrankwand) oder hängend mitten im Raum (z.B. von einer Lampe) platziert werden.</li>
        <li>Stellen Sie die Detektoren während der gesamten Messdauer nicht um.</li>
        <li>Versuchen Sie nicht das Gehäuse der Detektoren zu öffnen und platzieren Sie diese immer außer Reichweite von Kindern.</li>
      </ul>
    </div>
  </div>
  <div class="front-footer"></div>
</section>

<section class="sheet sheet--back">
  <div class="hero" role="img" aria-label="Foto einer fröhlichen Familie mit Hund in einem hellen Wohnraum">
    <div class="brand">
      <span class="brand-dot"></span>
      <span class="brand-name">Luftprüfer.de</span>
    </div>
  </div>

  <div class="back-body">
    <div class="step-row">
      <div class="step">
        <span class="step-badge">3</span>
        <div><div class="step-title">SCHRITT 3:</div><div class="step-sub">RADONMESSUNG</div></div>
      </div>
      <div class="partner">TESTOVAL</div>
    </div>
    <p>Die Radonmessung beginnt, sobald Sie die radondichten Verpackungen öffnen. <span class="red">Bitte halten Sie die Messdauer wie folgt ein:</span></p>

    <div class="duration">
      <div class="col col--left">
        <h3>Kurzzeitmessung:</h3>
        <ul class="dots">
          <li>Mindestmessdauer 10 Tage (bis hin zu 30 Tagen).</li>
          <li>Führen Sie die Messung vorzugsweise in der Heizperiode (1. Oktober – 30. April) durch.</li>
          <li>Kurzzeitmessungen werden oft beim Kauf oder Verkauf von Immobilien genutzt, um ein mögliches Gefährdungspotential abschätzen zu können, oder wenn die Zeit nicht ausreicht, um eine Langzeitmessung durchzuführen.</li>
        </ul>
      </div>
      <div class="col col--right">
        <h3>Langzeitmessung:</h3>
        <ul class="dots">
          <li>Mindestmessdauer 3 Monate während der Heizperiode (1. Oktober – 30. April).</li>
          <li>Um einen Jahresmittelwert der Radonkonzentration in Innenräumen ermitteln zu können, halten Sie die Messdauer von 12 Monaten ein.</li>
          <li>Falls Ihr Arbeitsplatz in einem Radon-Vorsorgegebiet liegt und somit der Messpflicht unterliegt, muss die Messdauer von 12 Monaten eingehalten werden.</li>
        </ul>
      </div>
    </div>

    <div class="step" style="margin-top:10px">
      <span class="step-badge">4</span>
      <div><div class="step-title">SCHRITT 4:</div><div class="step-sub">ABSCHLUSS DER RADONMESSUNG MIT ABSCHLIESSENDEM PRÜFBERICHT</div></div>
    </div>
    <p>Nach Ablauf der Messdauer, loggen Sie sich auf <span class="strong-red">https://kundenportal.testoval.se/de</span> in Ihrem Account ein. Vermerken Sie hier das Ende der Messung und senden Sie anschließend alle Radondetektoren ausreichend frankiert in einem Umschlag oder einem Karton zeitnah an unsere Rücksendeadresse:</p>

    <div class="address">
      <svg width="28" height="20" viewBox="0 0 28 20" fill="none" stroke="#d0232a" stroke-width="1.6"><rect x="1" y="1" width="26" height="18"/><path d="M1 1 L14 11 L27 1"/><path d="M1 19 L11 9M27 19 L17 9"/></svg>
      <p>Luftprüfer.de<br>Lindenstraße 14 – 28195 Musterhafen – Deutschland</p>
    </div>

    <p>Sobald die Radondetektoren im Labor von TESTOVAL eingetroffen sind, werden diese fachgerecht analysiert und die Ergebnisse der Radonmessung ausgewertet. Ein vollständiger Prüfbericht wird Ihnen innerhalb von 36 Stunden nach Erhalt der Detektoren im Labor per E-Mail zugeschickt.</p>

    <div class="hints">
      <div class="hints-inner">
        <h4>Weitere Hinweise:</h4>
        <div class="hints-cols">
          <ul class="dots" style="flex:1">
            <li>Bitte beachten Sie, dass die Radonmessung innerhalb von 15 Monaten nach Kaufdatum abgeschlossen sein muss.</li>
            <li>Versuchen Sie nicht das Gehäuse der Detektoren zu öffnen und platzieren Sie diese immer außer Reichweite von Kindern.</li>
            <li>Während der gesamten Messdauer dürfen die Detektoren nicht an einem anderen Ort umplatziert werden.</li>
          </ul>
          <ul class="dots" style="flex:1">
            <li>Durch die Anmeldung auf der Website <b>https://kundenportal.testoval.se/de</b> und die Eingabe der erforderlichen Daten bestätigt der/die Wohnungseigentümer*in/Messverantwortliche, dass er/sie die Messanleitung befolgt hat und die Detektoren gemäß den Anweisungen korrekt platziert wurden.</li>
          </ul>
        </div>
      </div>
    </div>
  </div>

  <footer class="back-footer">
    <p>Datenschutz (GDPR), Impressum und AGBs: Mehr Information dazu finden Sie unter www.luftprüfer.de</p>
  </footer>
</section>

</body>
</html>
```